Allied Health team of Physiotherapists & Occupational Therapists seek a business card design

We have our new logo, we now need our new business cards and stationary. Tidewell: Oedema & Family Clinic is seeking a generic card design to represent our whole team and individual cards for each therapist that incorporates our new logo to communicate our holistic approach that is calming, nuturing, supportive and welcoming.
Our Physiotherapists and Occupational Therapists assess, treat and provide education for people who are at risk of or who have lymphoedema. This is often as a result of treatment for cancer. We provide pre-operative and post-operative management and cancer rehabilitation in our Pilates studio. Our team also consists of Physiotherapists who have a strong interest in pelvic floor and continence management for both men and women.

Target Market(s)

Mainly women health conscious

Industry/Entity Type

Allied Health: Physiotherapy / Occupational Therapy

Contact Information for Business Card

Address: 14 Gallivant Ave Seacliff 3288 Phone: 84316570 fax: 8431 6578 Email: info@tidewellcareservices.com.au Website: tidewellcareservices.com.au Facebook address: /TidewellOedemaAndFamilyCareClinic. Room to write appointments. Individual cards need to have name, office email and individual email and professional details

Requirements
Must have
• Logo as per uploaded documents

```html
<!DOCTYPE html>
<html lang="en">
<head>
<meta charset="utf-8">
<title>Tidewell: Oedema &amp; Family Clinic – Business Card</title>
<link href="https://fonts.googleapis.com/css2?family=Montserrat:wght@300;400;500;600;700&display=swap" rel="stylesheet">
<style>
  :root {
    --peach: #f4a77b;
    --peach-light: #f7b994;
    --sage: #b9c0b2;
    --ink: #3a3a3a;
    --grey: #6d6d6d;
    --muted: #9a9a9a;
    --paper: #fbfbfa;
    --backdrop: #d9d9d9;
  }
  * { box-sizing: border-box; margin: 0; padding: 0; }
  html, body { width: 1200px; height: 1036px; overflow: hidden; }
  body {
    background: var(--backdrop);
    font-family: "Montserrat", Arial, sans-serif;
    position: relative;
  }
  .card {
    position: absolute;
    left: 180px;
    width: 840px;
    height: 480px;
    border-radius: 4px;
    overflow: hidden;
    box-shadow: 0 6px 18px rgba(0,0,0,.12);
  }
  /* Card back */
  .card--back {
    top: 23px;
    background: linear-gradient(120deg, var(--peach) 0%, var(--peach-light) 60%, var(--peach) 100%);
    color: #fff;
  }
  .brand-mark {
    position: absolute;
    display: flex;
    flex-direction: column;
    align-items: center;
    gap: 14px;
    text-align: center;
  }
  .brand-mark__ring {
    width: 26px; height: 26px;
    border-radius: 50%;
    border: 2px solid currentColor;
  }
  .brand-mark__name {
    font-weight: 500;
    letter-spacing: .06em;
    line-height: 1.3;
  }
  .card--back .brand-mark { left: 270px; top: 120px; width: 300px; }
  .card--back .brand-mark__name { font-size: 26px; }
  .social {
    position: absolute;
    left: 150px; bottom: 62px;
    display: flex; align-items: center; gap: 12px;
    font-size: 21px; font-weight: 400; letter-spacing: .01em;
  }
  .social__dot { width: 22px; height: 22px; border-radius: 50%; background: #fff; }
  /* Card front */
  .card--front { top: 533px; background: var(--paper); }
  .edge { position: absolute; }
  .edge--left { left: 0; top: 0; width: 16px; height: 100%; background: var(--peach); }
  .edge--bottom { left: 0; bottom: 0; width: 360px; height: 14px; background: var(--sage); }
  .edge--right-top { right: 0; top: 0; width: 22px; height: 56%; background: var(--sage); }
  .edge--right-bottom { right: 0; bottom: 0; width: 22px; height: 44%; background: var(--peach); }
  .card--front .brand-mark { left: 40px; top: 140px; width: 220px; color: var(--peach); }
  .card--front .brand-mark__name { font-size: 19px; }
  .profile { position: absolute; left: 330px; top: 48px; }
  .profile__name { font-size: 27px; color: var(--ink); letter-spacing: .01em; }
  .profile__first { font-weight: 700; }
  .profile__last { font-weight: 400; }
  .profile__roles {
    margin-top: 4px;
    color: var(--peach);
    font-weight: 600;
    font-size: 17px;
    line-height: 1.2;
  }
  .profile__quals {
    margin-top: 10px;
    color: var(--muted);
    font-size: 10.5px;
    line-height: 1.45;
  }
  .appointments { position: absolute; left: 420px; top: 200px; width: 360px; height: 100px; }
  .contact {
    position: absolute;
    left: 300px; top: 318px;
    color: var(--grey);
    font-size: 25px;
    line-height: 1.22;
    font-weight: 400;
  }
  .contact__row { display: flex; align-items: center; gap: 10px; }
  .contact__row--inset { padding-left: 30px; }
  .contact__icon { width: 22px; height: 22px; flex: none; }
  .contact__pair { display: flex; gap: 20px; }
  .contact__item { display: flex; align-items: center; gap: 8px; }
</style>
</head>
<body>

  <section class="card card--back" aria-label="Business card back">
    <div class="brand-mark">
      <span class="brand-mark__ring"></span>
      <span class="brand-mark__name">Tidewell: Oedema &amp; Family Clinic</span>
    </div>
    <div class="social">
      <span class="social__dot"></span>
      <span>/TidewellOedemaAndFamilyCareClinic</span>
    </div>
  </section>

  <section class="card card--front" aria-label="Business card front">
    <span class="edge edge--left"></span>
    <span class="edge edge--bottom"></span>
    <span class="edge edge--right-top"></span>
    <span class="edge edge--right-bottom"></span>

    <div class="brand-mark">
      <span class="brand-mark__ring"></span>
      <span class="brand-mark__name">Tidewell: Oedema &amp; Family Clinic</span>
    </div>

    <div class="profile">
      <h1 class="profile__name"><span class="profile__first">MAREN</span><span class="profile__last">HOLT</span></h1>
      <p class="profile__roles">Physiotherapist<br>Lymphoedema &amp; Oncology Rehabilitation<br>Continence &amp; Pelvic Floor</p>
      <p class="profile__quals">B. Physio (Hons), B.Sc (Exercise &amp; Health Science)<br>Grad Cert. Women's Exercise Therapy<br>Grad Cert. Pelvic Health &amp; Continence Care</p>
    </div>

    <svg class="appointments" viewBox="0 0 360 100" aria-label="Appointment writing lines">
      <line x1="0" y1="10" x2="0" y2="90" stroke="#9a9a9a" stroke-width="1"/>
      <line x1="20" y1="20" x2="360" y2="20" stroke="#9a9a9a" stroke-width="1"/>
      <line x1="20" y1="70" x2="360" y2="70" stroke="#9a9a9a" stroke-width="1"/>
    </svg>

    <div class="contact">
      <div class="contact__row">
        <svg class="contact__icon" viewBox="0 0 24 24"><path d="M12 3 2 12h3v9h5v-6h4v6h5v-9h3z" fill="#f4a77b"/></svg>
        <span>14 Gallivant Ave, Seacliff 3288</span>
      </div>
      <div class="contact__row contact__row--inset contact__pair">
        <span class="contact__item">
          <svg class="contact__icon" viewBox="0 0 24 24"><path d="M6.6 10.8a15 15 0 0 0 6.6 6.6l2.2-2.2c.3-.3.7-.4 1-.2 1.1.4 2.3.6 3.6.6.6 0 1 .4 1 1V20c0 .6-.4 1-1 1A17 17 0 0 1 3 4c0-.6.4-1 1-1h3.5c.6 0 1 .4 1 1 0 1.3.2 2.5.6 3.6.1.3 0 .7-.2 1z" fill="#f4a77b"/></svg>
          <span>8431 6570</span>
        </span>
        <span class="contact__item">
          <svg class="contact__icon" viewBox="0 0 24 24"><rect x="6" y="2" width="12" height="6" fill="#f4a77b"/><rect x="3" y="9" width="18" height="10" rx="2" fill="#f4a77b"/><rect x="7" y="15" width="10" height="7" fill="#fbfbfa" stroke="#f4a77b" stroke-width="1.5"/></svg>
          <span>8431 6578</span>
        </span>
      </div>
      <div class="contact__row">
        <svg class="contact__icon" viewBox="0 0 24 24"><rect x="2" y="5" width="20" height="14" rx="1" fill="#f4a77b"/><path d="m3 6 9 7 9-7" fill="none" stroke="#fbfbfa" stroke-width="1.5"/></svg>
        <span>info@tidewellcareservices.com.au</span>
      </div>
      <div class="contact__row">
        <svg class="contact__icon" viewBox="0 0 24 24"><circle cx="12" cy="12" r="10" fill="none" stroke="#f4a77b" stroke-width="2"/><ellipse cx="12" cy="12" rx="4.5" ry="10" fill="none" stroke="#f4a77b" stroke-width="1.6"/><line x1="2" y1="12" x2="22" y2="12" stroke="#f4a77b" stroke-width="1.6"/></svg>
        <span>tidewellcareservices.com.au</span>
      </div>
    </div>
  </section>

</body>
</html>
```